Label design for organic saffron, saffron and herbal syrup

We cultivate saffron, Damszen roses, flowers and herbs. We would need a recognizable outfit (label) for our products. Theoretically (and practically) we have "converted" the family coat of arms into a kind of LOGO. I would send this in the attachment. It would be nice if - in one way or another - this LOGO / coat of arms could be used (certainly with other colors). For some time we have played with the idea of changing the second part of the family name "Wallmoser" (in German .... greuth sounds similar to Kraut / herb [English]) .... eg Wallmoser's saffron syrup into the labeling.
Our products are primarily syrups, currently herbal syrup and saffron syrup. Here the first problem arises, the only bottles / caps that are actually approved for syrup filling (hot filling) are appallingly ugly (see attachment), the only possibility of "sprucing up" is to use so-called "shrink sleeves" (here we need a diameter of 31 and a length of about 40), the colors of which are also limited. Besides the syrup, we sell saffron as a spice and various herbal mixtures (see appendix current packaging saffron). Our quantities are small (syrup 200ml-330ml), saffron in the gram range.
We also need quasi the back of the labeling (this should be able to be redefined per charge) .... Batch 1 (with small quantity has eg more of herb xy than the next batch or the saffron syrup with batch xy needs more / less saffron). In addition, we are certified organic (for this reason, the reverse side would also have to contain all the requirements of organic labeling) [see attachment].
We do not really want to address a specific clientele. Maybe just people who want to taste, enjoy, mix drinks, cook .... (and - unfortunately - don't like Corvel syrup :-) and want to pay a bit more, or find our saffron or herbs better than others) .
In summary
- Strong recognition value (possibly inclusion of "coat of arms", color variable ... although I personally don't like yellow that much)
- Saffron syrup (the color of the saffron syrup is yellow / golden-yellow-light orange, in a transparent ugly bottle)
- Herbal syrup (color variable from blue / green / brown / red elements, in transparent ugly bottle)
Saffron and other herbs (very small containers, type of container not yet fixed)
Regarding a potential "style" I can unfortunately give little information. On the one hand, I am in love with minimalism, on the other hand, I find the translucent, cryptic, implied enormously attractive and sometimes even the "overloaded" colorful has its charm. I think that all in all, it just has to be coherent, and then it will be good.
Requirements
Must have
- Integration of Code of Arms, modifiable for different products

```html
<!DOCTYPE html>
<html lang="de">
<head>
<meta charset="utf-8">
<title>Wallmoser Rose Sirup Label</title>
<link rel="stylesheet" href="https://fonts.googleapis.com/css2?family=Great+Vibes&family=Zilla+Slab:wght@500&family=Open+Sans:wght@700&display=swap">
<style>
  :root {
    --plum: #7b1a4f;
    --plum-deep: #6a1544;
    --gold: #c9a24a;
    --gold-light: #e6cf86;
    --gold-dark: #a88235;
    --ink-navy: #23225f;
    --white: #ffffff;
    --badge-green: #c4dea0;
    --eu-green: #5aa12f;
    --black: #111111;
  }
  * { box-sizing: border-box; margin: 0; padding: 0; }
  html, body {
    width: 784px; height: 1200px; overflow: hidden;
    background: var(--white);
  }
  .label {
    position: absolute; left: 45px; top: 45px;
    width: 705px; height: 1109px;
    background: var(--plum);
    overflow: hidden;
    font-family: "Open Sans", Arial, sans-serif;
    color: var(--white);
  }
  .lace-band {
    position: absolute; left: 0; top: 0; width: 705px; height: 353px;
    background:
      radial-gradient(ellipse at 15% 30%, rgba(201,162,74,0.45), transparent 55%),
      radial-gradient(ellipse at 88% 40%, rgba(201,162,74,0.45), transparent 55%),
      radial-gradient(ellipse at 50% 90%, rgba(201,162,74,0.25), transparent 60%),
      var(--plum-deep);
  }
  .gold-bar {
    position: absolute; left: 0; top: 353px; width: 705px; height: 24px;
    background: linear-gradient(180deg, var(--gold-light), var(--gold) 45%, var(--gold-dark));
  }
  .bottle-window { position: absolute; left: 194px; top: 0; width: 313px; height: 353px; }
  .brand-mark {
    position: absolute; left: 306px; top: 150px; width: 90px; height: 90px;
    border: 3px solid var(--ink-navy); border-radius: 50%;
  }
  .brand-name {
    position: absolute; left: 194px; top: 262px; width: 313px;
    text-align: center;
    font-family: "Great Vibes", cursive;
    font-size: 58px; line-height: 70px;
    color: var(--ink-navy);
  }
  .product-arch { position: absolute; left: 194px; top: 377px; width: 313px; height: 354px; }
  .rose-drawing {
    position: absolute; left: 215px; top: 400px; width: 270px; height: 400px;
    border-radius: 50% 50% 40% 40%;
    background: radial-gradient(ellipse at 50% 30%, rgba(214,150,180,0.28), rgba(214,150,180,0.08) 55%, transparent 75%);
  }
  .product-name {
    position: absolute; left: 194px; top: 450px; width: 313px;
    text-align: center;
    font-family: "Zilla Slab", Georgia, serif;
    font-weight: 500;
    font-size: 74px; line-height: 94px;
    color: var(--white);
  }
  .vertical {
    position: absolute;
    writing-mode: vertical-rl;
    transform: rotate(180deg);
    font-weight: 700;
  }
  .ingredients {
    left: 33px; top: 418px; width: 83px; height: 645px;
    font-size: 15px; line-height: 19px;
    text-align: center;
    letter-spacing: 0.2px;
  }
  .producer {
    left: 604px; top: 424px; width: 68px; height: 404px;
    font-size: 14px; line-height: 18px;
    text-align: start;
  }
  .producer .organic-note { margin-left: 12px; }
  .best-before {
    position: absolute; left: 600px; top: 877px; width: 84px; height: 189px;
    background: var(--white);
  }
  .best-before .vertical {
    left: 6px; top: 8px; width: 26px; height: 173px;
    color: var(--black); font-size: 16px; line-height: 24px;
  }
  .volume, .ratio {
    position: absolute; top: 1040px;
    font-size: 19px; font-weight: 700; line-height: 24px;
  }
  .volume { left: 212px; }
  .ratio { left: 420px; }
  .organic-badge {
    position: absolute; left: 298px; top: 892px; width: 99px; height: 174px;
    background: var(--badge-green);
    border: 2px solid var(--gold);
  }
  .organic-badge .seal {
    position: absolute; left: 20px; top: 10px; width: 58px; height: 58px;
    background: var(--white); border-radius: 8px;
  }
  .organic-badge .seal::after {
    content: ""; position: absolute; left: 9px; top: 9px; width: 40px; height: 40px;
    border-radius: 50%; background: #3f8f3a;
  }
  .organic-badge .leaf-flag {
    position: absolute; left: 10px; top: 80px; width: 78px; height: 52px;
    background: var(--eu-green);
  }
</style>
</head>
<body>
  <div class="label">
    <div class="lace-band" role="img" aria-label="Gold lace ornament pattern on plum background"></div>

    <svg class="bottle-window" viewBox="0 0 313 353" aria-hidden="true">
      <path d="M98,0 H215 V38 C215,56 240,62 262,76 C296,100 313,140 313,190 V353 H0 V190 C0,140 17,100 51,76 C73,62 98,56 98,38 Z"
            fill="#ffffff" stroke="#c9a24a" stroke-width="3"/>
    </svg>
    <div class="brand-mark"></div>
    <div class="brand-name">Wallmoser</div>

    <div class="gold-bar"></div>

    <div class="rose-drawing" role="img" aria-label="Faint line drawing of a rose with stem and leaves"></div>
    <svg class="product-arch" viewBox="0 0 313 354" aria-hidden="true">
      <path d="M3,0 V197 A153.5,153.5 0 0 0 310,197 V0" fill="none" stroke="#c9a24a" stroke-width="3"/>
    </svg>
    <h1 class="product-name">Rose<br>Sirup</h1>

    <p class="vertical ingredients">ZUTATEN: Lorem ipsum dolor sit amet, consectetur adipiscing elit. Morbi ultricies molestie orci. Aenean purus mauris, sodales nec diam dignissim, porttitor laoreet enim. Aliquam id sollicitudin turpis. Vivamus aliquet elit sem, et ornare ex aliquam in.</p>

    <div class="vertical producer">
      <p class="organic-note">*aus kontrolliert biologischer Landwirtschaft</p>
      <p>Expertly crafted by: Halden-Wallmoser</p>
      <p>1234 Street Name, Any City, District, Country</p>
    </div>

    <div class="best-before">
      <p class="vertical">Best Before:</p>
    </div>

    <span class="volume">300mL</span>
    <div class="organic-badge" role="img" aria-label="Organic certification seals">
      <div class="seal"></div>
      <div class="leaf-flag"></div>
    </div>
    <span class="ratio">1:7</span>
  </div>
</body>
</html>
```